Evaporative Air Conditioning Summer Service

Would like to design a flyer to send out in an email to existing clients to promote a Pre-summer service for Evaporative Air Conditioners
Cost will be $110.00 inc gst
Tasks included in service are
- Inspection and clean of pads
- Inspection and check float valve, water pump, fan, motor, bearings, drain
- Clean basin
- Supply of bacterial tablet
- Inspect overall condition of unit
- Any repairs if required will be quoted
Please see files attached of a previous very basic flyer I have used for installation and replacement unit costs. This has current contact information
Have also uploaded company logo for use.
Thanks
Plumbing

```html
<!DOCTYPE html>
<html lang="en">
<head>
<meta charset="utf-8">
<title>Pre-Summer Evaporative Air Conditioner Service</title>
<link rel="stylesheet" href="https://fonts.googleapis.com/css2?family=Montserrat:wght@500;600;800&family=Anton&display=swap">
<style>
  :root{
    --canvas:#e7e8ea;
    --paper:#fbfbfb;
    --blue:#1f3fa8;
    --blue-deep:#2a3fae;
    --blue-light:#1a7fc4;
    --orange:#ee7d1a;
    --amber:#f6a417;
    --yellow:#ffd200;
    --ink:#1b1b1b;
    --white:#ffffff;
  }
  *{box-sizing:border-box;margin:0;padding:0}
  html,body{width:676px;height:1200px;overflow:hidden;background:var(--canvas)}
  body{font-family:"Montserrat",Arial,sans-serif;position:relative}
  .flyer{position:absolute;left:18px;top:147px;width:640px;height:905px;background:linear-gradient(160deg,#ffffff,#f1f1f1);overflow:hidden;box-shadow:0 8px 24px rgba(0,0,0,.12)}
  .brand{position:absolute;left:42px;top:78px;display:flex;align-items:center;gap:12px}
  .brand-mark{width:22px;height:22px;border-radius:50%;background:var(--orange)}
  .brand-name{font-weight:800;font-size:28px;color:var(--blue);letter-spacing:.5px}
  .band{position:absolute;left:0;top:151px;width:640px;height:243px;background:linear-gradient(170deg,var(--blue-deep) 35%,var(--blue-light) 100%)}
  .accent{position:absolute;left:592px;top:10px;width:48px;height:390px;background:linear-gradient(180deg,var(--yellow),var(--amber) 60%,var(--orange))}
  .headline{position:absolute;left:38px;top:181px;color:var(--white);font-weight:800;font-size:33px;line-height:37.8px;letter-spacing:-.4px}
  .divider{position:absolute;left:380px;top:188px;width:1px;height:138px;background:rgba(255,255,255,.7)}
  .price{position:absolute;left:404px;top:184px;color:var(--white)}
  .price-label{font-weight:600;font-size:17px}
  .price-value{display:block;font-family:"Anton",Impact,sans-serif;font-size:104px;line-height:98px;color:var(--yellow);transform:scaleX(.62);transform-origin:left;letter-spacing:-2px;margin-top:2px}
  .price-tax{font-weight:600;font-size:17px;margin-left:6px}
  .unit{position:absolute;left:35px;top:336px;width:288px;height:94px;border-radius:4px;background:linear-gradient(180deg,#ffffff 0%,#f0f2f4 70%,#b9bec4 100%);box-shadow:0 6px 10px rgba(0,0,0,.25)}
  .tasks{position:absolute;left:38px;top:418px;display:grid;grid-template-columns:repeat(3,181px);grid-template-rows:repeat(2,179px);gap:9px}
  .task{border-radius:6px;color:var(--white);display:flex;flex-direction:column;align-items:center;justify-content:center;text-align:center;font-weight:500;font-size:16.5px;line-height:18.5px;padding:0 8px;gap:10px}
  .task--orange{background:var(--orange)}
  .task--blue{background:var(--blue)}
  .task svg{width:58px;height:58px;fill:none;stroke:var(--white);stroke-width:2;stroke-linecap:round;stroke-linejoin:round}
  .contact{position:absolute;left:0;width:640px;text-align:center;top:802px}
  .phone{display:inline-flex;align-items:center;gap:10px;font-weight:800;font-size:29px;color:var(--blue)}
  .phone svg{width:30px;height:30px;fill:none;stroke:var(--orange);stroke-width:2}
  .email,.abn{font-weight:500;font-size:19px;color:var(--ink);line-height:24px}
  .email{margin-top:2px}
</style>
</head>
<body>
<main class="flyer">
  <div class="brand"><span class="brand-mark"></span><span class="brand-name">SUMMIT GAS &amp; PLUMBING</span></div>

  <div class="band"></div>
  <div class="accent" role="img" aria-label="Decorative orange and yellow flame ornament along the right edge"></div>

  <h1 class="headline">PRE-SUMMER<br>SERVICE FOR<br>EVAPORATIVE AIR<br>CONDITIONERS</h1>
  <div class="divider"></div>
  <div class="price">
    <div class="price-label">Cost will be</div>
    <span class="price-value">$110.00</span>
    <div class="price-tax">inc gst.</div>
  </div>

  <div class="unit" role="img" aria-label="White wall-mounted air conditioning unit"></div>

  <section class="tasks">
    <div class="task task--orange">
      <svg viewBox="0 0 52 52"><rect x="12" y="10" width="22" height="28" rx="3"/><path d="M16 18h14M16 24h14M16 30h14"/><path d="M40 12l2 4 4 2-4 2-2 4-2-4-4-2 4-2z"/></svg>
      <span>Inspection and<br>clean of pads</span>
    </div>
    <div class="task task--blue">
      <svg viewBox="0 0 52 52"><circle cx="30" cy="20" r="13"/><path d="M24 20l4 4 8-8"/><path d="M21 29L9 42"/></svg>
      <span>Inspection and<br>check float valve,<br>water pump, fan,<br>motor, bearings,<br>drain</span>
    </div>
    <div class="task task--orange">
      <svg viewBox="0 0 52 52"><path d="M8 26h36v4a18 12 0 0 1-36 0z"/><path d="M26 26V12a4 4 0 0 1 8 0v2"/><path d="M23 42v6h6v-6"/></svg>
      <span>Clean basin</span>
    </div>
    <div class="task task--blue">
      <svg viewBox="0 0 52 52"><rect x="6" y="16" width="14" height="30" rx="7" transform="rotate(35 13 31)"/><ellipse cx="36" cy="36" rx="10" ry="4"/><path d="M26 36v5a10 4 0 0 0 20 0v-5"/><circle cx="40" cy="16" r="5"/></svg>
      <span>Supply of<br>bacterial tablet</span>
    </div>
    <div class="task task--orange">
      <svg viewBox="0 0 52 52"><rect x="4" y="8" width="44" height="18" rx="3"/><path d="M8 22h36"/><circle cx="38" cy="14" r="2"/><path d="M18 30c-4 4 4 6 0 12M26 30c-4 4 4 6 0 12M34 30c-4 4 4 6 0 12"/></svg>
      <span>Inspect overall<br>condition of unit</span>
    </div>
    <div class="task task--blue">
      <svg viewBox="0 0 52 52"><path d="M10 42l22-22a8 8 0 0 0 10-10l-5 5-4-4 5-5a8 8 0 0 0-10 10L6 38z"/><path d="M42 42L22 22M14 8l6 6-4 4-6-6z"/></svg>
      <span>Any repairs if<br>required will<br>be quoted</span>
    </div>
  </section>

  <footer class="contact">
    <div class="phone">
      <svg viewBox="0 0 28 28"><path d="M6 3l5 1 2 6-3 2a14 14 0 0 0 6 6l2-3 6 2 1 5-3 3C12 25 3 16 3 6z"/><path d="M17 4a8 8 0 0 1 7 7M17 8a4 4 0 0 1 3 3"/></svg>
      <span>0400 555 019</span>
    </div>
    <p class="email">admin@summitgasplumbing.example</p>
    <p class="abn">ABN 00 000 000 000</p>
  </footer>
</main>
</body>
</html>
```